Travel Agency Website - Simple General

Need a 7 page simple design that is pretty repetitive. Need to be able to load quickly that is SEO optimized. Trying to give ideas on what they can do, be personal as we are local, but at the same time come across as professional and get information easily with little burden.

- Landing Page
- Brimwell Vacations Page
- Family Trips
- Road Trips from Texas
- Other Destinations
- About Us Page
- Contact Us Page

Target Market(s)

Families

Coding

Coded - Design and coding required

Number of Pages Required

5+ page

Colors

Designer to choose colors to be used in the design.

Requirements
Must have
• Like it to flow easily with our logo. Use that for colors, etc.

```html
<!DOCTYPE html>
<html lang="en">
<head>
<meta charset="utf-8">
<title>Lantern Trail Travel</title>
<link rel="stylesheet" href="https://fonts.googleapis.com/css2?family=Cormorant+Garamond:wght@500;600&family=Nunito+Sans:wght@400;600;700;800&display=swap">
<style>
:root{
  --teal:#1b5e68;
  --teal-dark:#174f58;
  --gold:#c98f48;
  --cream:#fffcf5;
  --mint:#e1efec;
  --ink:#2a2a2a;
  --muted:#4f5f63;
  --serif:"Cormorant Garamond",Georgia,serif;
  --sans:"Nunito Sans",Arial,sans-serif;
}
*{box-sizing:border-box;margin:0;padding:0}
html,body{width:696px;height:1200px;overflow:hidden;background:var(--cream);font-family:var(--sans);color:var(--ink)}
.page{position:relative;width:696px;height:1200px;overflow:hidden}
.abs{position:absolute}

.topbar{left:0;top:0;width:696px;height:16px;background:var(--teal);color:#fff;font-size:7px}
.topbar span{position:absolute;top:4px;display:flex;align-items:center;gap:3px}
.navbar{left:0;top:16px;width:696px;height:28px;background:var(--cream);z-index:2}
.nav-group{position:absolute;top:9px;display:flex;gap:9px;white-space:nowrap}
.nav-left{left:83px}
.nav-right{right:84px;gap:10px}
.nav-link{font-size:7.8px;color:var(--ink);text-decoration:none}
.nav-link.active{color:var(--gold)}
.brand-badge{left:298px;top:2px;width:100px;height:66px;border-radius:50%;background:var(--cream);z-index:3;display:flex;align-items:center;justify-content:center;text-align:center;font-family:var(--serif);font-weight:600;color:var(--teal);font-size:12px;line-height:1.05}

.hero{left:0;top:43px;width:696px;height:360px;background:linear-gradient(180deg,#6f8aa0 0%,#b99b84 30%,#6f8c98 45%,#c6a58a 70%,#a98468 100%)}
.hero-wave{left:0;top:340px;width:696px;height:64px}
.hero-title{left:83px;top:100px;font-family:var(--serif);font-weight:500;font-size:37px;line-height:48px;color:#fff}
.hero-sub{left:83px;top:206px;font-size:10.5px;line-height:18.5px;color:#fff}
.dots{left:41px;top:188px;display:flex;flex-direction:column;gap:5px}
.dots i{width:5px;height:5px;border-radius:50%;background:rgba(255,255,255,.55)}
.dots i:first-child{background:#fff}
.btn{display:flex;align-items:center;justify-content:center;gap:4px;background:var(--gold);color:#fff;font-weight:800;border-radius:3px;text-transform:uppercase}
.hero-btn{left:83px;top:263px;width:149px;height:28px;font-size:9.5px}

.about-mark{left:76px;top:419px;width:264px;height:229px;display:flex;align-items:center;justify-content:center;text-align:center;font-family:var(--serif);font-weight:600;color:var(--teal);font-size:40px;line-height:1}
.about-title{left:378px;top:418px;font-family:var(--serif);font-weight:500;font-size:25px;line-height:28px;color:var(--teal)}
.gold{color:var(--gold)}
.about-text{left:380px;top:486px;width:232px;font-size:7.4px;line-height:13.4px;color:var(--muted);text-align:justify}
.about-text p+p{margin-top:6px}
.about-btn{left:380px;top:606px;width:88px;height:26px;font-size:8.5px}

.journey-title{left:0;top:684px;width:696px;text-align:center;font-family:var(--serif);font-weight:500;font-size:25px;color:var(--teal)}

.tab{background:#fff;display:flex;align-items:center;justify-content:center;font-size:10px;color:var(--ink)}
.tab-left{left:83px;top:758px;width:34px;height:140px;border-radius:7px 0 0 7px}
.tab-left span{transform:rotate(-90deg);white-space:nowrap}
.tab-right{left:579px;top:758px;width:33px;height:140px;border-radius:0 7px 7px 0}
.tab-right span{transform:rotate(90deg);white-space:nowrap}
.photo-family{left:116px;top:758px;width:81px;height:140px;background:linear-gradient(160deg,#8fc3d6,#e8b79c 55%,#d9c3a6)}
.photo-park{left:196px;top:751px;width:172px;height:153px;border-radius:9px 0 0 9px;background:linear-gradient(180deg,#5aa3e0 0%,#7fb7d8 35%,#2f6b58 60%,#6d5a5a 100%)}
.photo-road{left:500px;top:758px;width:80px;height:140px;background:linear-gradient(180deg,#b7c9d2,#7f9a78 40%,#3b3f46 70%,#8e99a8)}
.card{left:366px;top:743px;width:135px;height:170px;background:var(--teal);border-radius:9px;color:#fff;padding:15px 17px}
.card h3{font-weight:400;font-size:10.5px;line-height:16px}
.card p{margin-top:9px;font-size:7.4px;line-height:13.4px}
.card a{display:flex;align-items:center;gap:5px;margin-top:12px;color:var(--gold);font-weight:800;font-size:8.5px;text-decoration:none}
.arrow{width:22px;height:22px;border-radius:50%;border:1px solid #d8d8d8;background:#fff;display:flex;align-items:center;justify-content:center}

.footer-bg{left:0;top:940px;width:696px;height:260px}
.footer-mark{left:81px;top:1015px;width:118px;height:103px;display:flex;align-items:center;justify-content:center;text-align:center;font-family:var(--serif);font-weight:600;color:var(--teal);font-size:20px;line-height:1}
.foot-head{font-weight:700;font-size:9px;color:var(--teal);letter-spacing:.2px}
.foot-list{list-style:none;margin-top:10px}
.foot-list li{display:flex;align-items:center;gap:7px;font-size:7.8px;height:14px}
.foot-list li::before{content:"";width:6px;height:6px;border-radius:50%;background:var(--gold)}
.contact-row{position:absolute;left:0;display:flex;gap:6px;font-size:7.8px;line-height:12px}
.contact-row .ico{width:16px;height:16px;border-radius:50%;background:var(--gold);display:flex;align-items:center;justify-content:center;flex:none}
.divider{left:81px;top:1146px;width:529px;height:1px;background:#c9dcd8}
.copy{left:0;top:1155px;width:696px;text-align:center;font-size:7.8px;color:var(--muted)}
.social{top:1173px;width:17px;height:17px;border-radius:50%;background:var(--teal)}
</style>
</head>
<body>
<div class="page">

  <div class="abs topbar">
    <span style="left:414px"><svg width="7" height="5" viewBox="0 0 7 5"><rect width="7" height="5" rx=".6" fill="#fff"/><path d="M0 .4 3.5 3 7 .4" stroke="#1b5e68" stroke-width=".7" fill="none"/></svg>info@lanterntrailtravel.com</span>
    <span style="left:558px"><svg width="6" height="6" viewBox="0 0 24 24"><path fill="#fff" d="M6.6 10.8a15 15 0 0 0 6.6 6.6l2.2-2.2c.3-.3.7-.4 1-.2 1.1.4 2.3.6 3.6.6.6 0 1 .4 1 1V20c0 .6-.4 1-1 1A17 17 0 0 1 3 4c0-.6.4-1 1-1h3.5c.6 0 1 .4 1 1 0 1.2.2 2.4.6 3.6.1.3 0 .7-.2 1z"/></svg>111.111.1111</span>
  </div>

  <nav class="abs navbar">
    <div class="nav-group nav-left">
      <a class="nav-link active">Home</a>
      <a class="nav-link">Brimwell Vacations</a>
      <a class="nav-link">Family Trips</a>
      <a class="nav-link">About Us</a>
    </div>
    <div class="nav-group nav-right">
      <a class="nav-link">Road Trips from Texas</a>
      <a class="nav-link">Other Destination</a>
      <a class="nav-link">Contact Us</a>
    </div>
  </nav>
  <div class="abs brand-badge">Lantern Trail<br>Travel</div>

  <div class="abs hero" role="img" aria-label="Family walking hand in hand along a beach at sunset"></div>
  <svg class="abs hero-wave" viewBox="0 0 696 64" preserveAspectRatio="none"><path d="M0 25C60 18 110 20 160 40S250 66 320 50 410 10 480 14 620 50 696 48V64H0Z" fill="#fffcf5"/></svg>
  <div class="abs dots"><i></i><i></i><i></i><i></i></div>
  <h1 class="abs hero-title">Lantern Trail<br>Travel</h1>
  <p class="abs hero-sub">Travel planning made magical, memorable,<br>and completely stress-free.</p>
  <a class="abs btn hero-btn">Start Your Plan Trip <svg width="5" height="7" viewBox="0 0 5 7"><path d="M1 1l2.5 2.5L1 6" stroke="#fff" stroke-width="1.2" fill="none"/></svg></a>

  <div class="abs about-mark">Lantern Trail<br>Travel</div>
  <h2 class="abs about-title"><span class="gold">About</span> Lantern Trail<br>Travel</h2>
  <div class="abs about-text">
    <p>Lorem ipsum dolor sit amet, consectetur adipiscing elit, sed do eiusmod tempor incididunt ut labore et dolore magna aliqua. Ut enim ad minim veniam, quis nostrud exercitation ullamco laboris nisi ut aliquip ex ea commodo consequat.</p>
    <p>Duis aute irure dolor in reprehenderit in voluptate velit esse cillum dolore eu fugiat nulla pariatur. Excepteur sint occaecat cupidatat non proident, sunt in culpa qui.</p>
  </div>
  <a class="abs btn about-btn">Learn More <svg width="5" height="7" viewBox="0 0 5 7"><path d="M1 1l2.5 2.5L1 6" stroke="#fff" stroke-width="1.2" fill="none"/></svg></a>

  <h2 class="abs journey-title">Start Your <span class="gold">Journey</span> Into Something <span class="gold">Magical</span></h2>

  <div class="abs arrow" style="left:46px;top:817px"><svg width="6" height="9" viewBox="0 0 6 9"><path d="M5 1 1.5 4.5 5 8" stroke="#222" stroke-width="1.3" fill="none"/></svg></div>
  <div class="abs arrow" style="left:628px;top:817px"><svg width="6" height="9" viewBox="0 0 6 9"><path d="M1 1l3.5 3.5L1 8" stroke="#222" stroke-width="1.3" fill="none"/></svg></div>

  <div class="abs tab tab-left"><span>Family Trips</span></div>
  <div class="abs photo-family" role="img" aria-label="Family playing together at the beach"></div>
  <div class="abs photo-park" role="img" aria-label="Crowd entering a theme park gate on a sunny day"></div>
  <div class="abs card">
    <h3>Brimwell Vacations<br>Land and Sea</h3>
    <p>Lorem ipsum dolor sit amet, consectetur adipiscing elit, sed do eiusmod tempor incididunt ut labore et dolore magna aliqua enim ad.</p>
    <a>LEARN MORE <svg width="5" height="7" viewBox="0 0 5 7"><path d="M1 1l2.5 2.5L1 6" stroke="#c98f48" stroke-width="1.2" fill="none"/></svg></a>
  </div>
  <div class="abs photo-road" role="img" aria-label="Friends in a convertible driving a scenic road"></div>
  <div class="abs tab tab-right"><span>Texas Road Trips</span></div>

  <svg class="abs footer-bg" viewBox="0 0 696 260" preserveAspectRatio="none"><path d="M0 15C60 0 110 20 170 40S290 65 360 48 470 0 540 10 640 45 696 40V260H0Z" fill="#e1efec"/></svg>
  <div class="abs footer-mark">Lantern Trail<br>Travel</div>

  <div class="abs" style="left:283px;top:1016px">
    <div class="foot-head">MAIN PAGES</div>
    <ul class="foot-list">
      <li>Home</li><li>Brimwell Vacations</li><li>Family Trips</li><li>About Us</li><li>Texas Road Trips</li><li>Other Destinations</li><li>Contact Us</li>
    </ul>
  </div>

  <div class="abs" style="left:445px;top:1018px;width:170px;height:110px">
    <div class="foot-head">CONTACT DETAILS</div>
    <div class="contact-row" style="top:22px"><span class="ico"><svg width="8" height="8" viewBox="0 0 24 24"><path fill="#fff" d="M6.6 10.8a15 15 0 0 0 6.6 6.6l2.2-2.2c.3-.3.7-.4 1-.2 1.1.4 2.3.6 3.6.6.6 0 1 .4 1 1V20c0 .6-.4 1-1 1A17 17 0 0 1 3 4c0-.6.4-1 1-1h3.5c.6 0 1 .4 1 1 0 1.2.2 2.4.6 3.6.1.3 0 .7-.2 1z"/></svg></span><span style="padding-top:2px">111.111.1111</span></div>
    <div class="contact-row" style="top:46px"><span class="ico"><svg width="8" height="6" viewBox="0 0 7 5"><rect width="7" height="5" rx=".6" fill="#fff"/><path d="M0 .4 3.5 3 7 .4" stroke="#c98f48" stroke-width=".7" fill="none"/></svg></span><span style="padding-top:2px">hello@lanterntrailtravel.com</span></div>
    <div class="contact-row" style="top:71px"><span class="ico"><svg width="7" height="9" viewBox="0 0 10 14"><path fill="#fff" d="M5 0a5 5 0 0 0-5 5c0 3.8 5 9 5 9s5-5.2 5-9a5 5 0 0 0-5-5zm0 7a2 2 0 1 1 0-4 2 2 0 0 1 0 4z"/></svg></span><span style="padding-top:2px">123 Lorem ipsum dolor sit amet<br>Sed do 45678 USA</span></div>
  </div>

  <div class="abs divider"></div>
  <p class="abs copy">© 2026 Copyright&nbsp; Lantern Trail Travel.</p>
  <span class="abs social" style="left:329px" aria-label="Social link"></span>
  <span class="abs social" style="left:350px" aria-label="Social link"></span>

</div>
</body>
</html>
```